Need Flyer for Our Real estate Agency

Need to run General Campaign for our agency with Start of New Year as our theme ..Must have an agent's picture on the DL..
Address:
27 / 486Brindle rd, Marsden VIC 3047
Ph:03 9412 7306
email:info@kovalinrealestate.com.au
www.kovalinrealestate.com.au
Something like as attached picture..
Target Market(s)
Home Buyers
Industry/Entity Type
Real Estate Agent
Requirements
Must have
- Our Logo Colours

```html
<!DOCTYPE html>
<html lang="en">
<head>
<meta charset="utf-8">
<title>Kovalin Real Estate – New Year Campaign</title>
<link rel="stylesheet" href="https://fonts.googleapis.com/css2?family=Lato:wght@300;400;700;900&display=swap">
<style>
  :root {
    --page: #d3d4d6;
    --navy-deep: #0b1a4a;
    --navy: #16306e;
    --navy-mid: #1e3d86;
    --maroon: #7a1c24;
    --white: #ffffff;
    --photo-sky: #8fa9c9;
    --photo-house: #c9c3b8;
    --photo-suit: #2f4a7a;
    --photo-dark: #1b2a44;
    --photo-light: #dcdde0;
    --house-red: #d8544c;
  }
  * { margin: 0; padding: 0; box-sizing: border-box; }
  html, body { width: 1200px; height: 1190px; overflow: hidden; }
  body {
    background: var(--page);
    font-family: "Lato", "Helvetica Neue", Arial, sans-serif;
    color: var(--white);
    position: relative;
  }
  .card {
    position: absolute;
    left: 57px;
    width: 1066px;
    height: 506px;
    overflow: hidden;
    box-shadow: 0 6px 14px rgba(0,0,0,0.18);
  }
  .card--front { top: 51px; }
  .card--back { top: 636px; }
  .card__bg { position: absolute; inset: 0; display: block; }

  .brand {
    position: absolute;
    display: flex;
    align-items: center;
    gap: 14px;
    font-weight: 400;
    letter-spacing: 6px;
    color: var(--white);
  }
  .brand__mark { width: 16px; height: 16px; background: var(--white); }

  .card--front .brand { left: 0; width: 590px; justify-content: center; top: 118px; font-size: 58px; }
  .headline {
    position: absolute; left: 0; width: 590px; top: 228px;
    text-align: center; font-weight: 300; font-size: 35px; line-height: 50px;
  }
  .tagline {
    position: absolute; left: 0; width: 590px; top: 354px;
    text-align: center; font-size: 17.5px; font-weight: 400; letter-spacing: 0.2px;
  }
  .tagline strong { font-weight: 900; }
  .call-button {
    position: absolute; left: 94px; top: 409px; width: 400px; height: 52px;
    background: var(--white); border-radius: 26px;
    display: flex; align-items: center; justify-content: center; gap: 10px;
    color: var(--maroon); font-weight: 900; font-size: 23px;
    box-shadow: 0 3px 6px rgba(0,0,0,0.25);
  }
  .call-button svg { width: 24px; height: 24px; }
  .appraisal-note {
    position: absolute; left: 94px; width: 400px; top: 470px;
    text-align: center; font-size: 18.5px; font-weight: 400;
  }

  .card--back .brand { left: 560px; width: 430px; justify-content: center; top: 120px; font-size: 62px; }
  .agent-title { position: absolute; left: 612px; top: 242px; font-size: 23px; font-weight: 300; }
  .contact-list { position: absolute; left: 612px; top: 290px; list-style: none; }
  .contact-list li {
    display: flex; align-items: center; gap: 12px;
    height: 39.5px; font-size: 20px; font-weight: 300;
  }
  .contact-list svg { width: 20px; height: 20px; flex: none; }
  .office-address {
    position: absolute; left: 430px; width: 636px; top: 455px;
    text-align: center; font-size: 20px; font-weight: 300; letter-spacing: 0.3px;
  }
</style>
</head>
<body>

<section class="card card--front">
  <svg class="card__bg" viewBox="0 0 1066 506" aria-hidden="false">
    <defs>
      <linearGradient id="navyFront" x1="0" y1="0" x2="1" y2="1">
        <stop offset="0" stop-color="var(--navy-mid)"/>
        <stop offset="0.6" stop-color="var(--navy)"/>
        <stop offset="1" stop-color="var(--navy-deep)"/>
      </linearGradient>
      <linearGradient id="agentPhoto" x1="0" y1="0" x2="0" y2="1">
        <stop offset="0" stop-color="var(--photo-sky)"/>
        <stop offset="0.45" stop-color="var(--photo-house)"/>
        <stop offset="0.7" stop-color="var(--photo-suit)"/>
        <stop offset="1" stop-color="var(--photo-dark)"/>
      </linearGradient>
    </defs>
    <rect class="panel-navy" width="1066" height="506" fill="url(#navyFront)"/>
    <rect class="band-rule" x="0" y="428" width="720" height="3" fill="var(--white)"/>
    <rect class="band-maroon" x="0" y="434" width="720" height="72" fill="var(--maroon)"/>
    <path class="photo-frame" d="M 735 0 L 770 0 Q 590 250 655 506 L 622 506 Q 555 250 735 0 Z" fill="var(--white)"/>
    <path class="agent-photo" role="img" aria-label="Photo of the sales agent in a suit standing in front of a lit family home"
          d="M 770 0 L 1066 0 L 1066 506 L 655 506 Q 590 250 770 0 Z" fill="url(#agentPhoto)"/>
  </svg>

  <div class="brand"><span class="brand__mark"></span>KOVALIN</div>
  <p class="headline">Curios to know what your<br>home is worth?</p>
  <p class="tagline">START THE NEW YEAR WITH <strong>DEVAN MEHRA</strong> AND FIND OUT!</p>
  <div class="call-button">
    <span>CALL ME NOW!</span>
    <svg viewBox="0 0 24 24"><circle cx="12" cy="12" r="10.5" fill="none" stroke="var(--maroon)" stroke-width="2"/><path d="M8.5 6.5l2 2.2-1.1 1.6c.7 1.6 2 2.9 3.6 3.6l1.6-1.1 2.2 2-1.2 2c-4.3-.4-8.1-4.2-8.5-8.5z" fill="var(--maroon)"/></svg>
    <span>0431 578 219</span>
  </div>
  <p class="appraisal-note">For Free property Appraisal</p>
</section>

<section class="card card--back">
  <svg class="card__bg" viewBox="0 0 1066 506">
    <defs>
      <linearGradient id="navyBack" x1="1" y1="0" x2="0" y2="1">
        <stop offset="0" stop-color="var(--navy-mid)"/>
        <stop offset="0.55" stop-color="var(--navy)"/>
        <stop offset="1" stop-color="var(--navy-deep)"/>
      </linearGradient>
      <linearGradient id="handsPhoto" x1="0" y1="0" x2="1" y2="1">
        <stop offset="0" stop-color="var(--photo-dark)"/>
        <stop offset="0.4" stop-color="var(--house-red)"/>
        <stop offset="0.65" stop-color="var(--photo-light)"/>
        <stop offset="1" stop-color="var(--photo-suit)"/>
      </linearGradient>
    </defs>
    <rect class="panel-navy" width="1066" height="506" fill="url(#navyBack)"/>
    <rect class="band-rule" x="380" y="427" width="686" height="3" fill="var(--white)"/>
    <rect class="band-maroon" x="380" y="433" width="686" height="73" fill="var(--maroon)"/>
    <path class="photo-frame" d="M 330 0 L 372 0 Q 585 250 462 506 L 425 506 Q 540 250 330 0 Z" fill="var(--white)"/>
    <path class="hands-photo" role="img" aria-label="Photo of two hands sheltering a small red model house"
          d="M 0 0 L 330 0 Q 540 250 425 506 L 0 506 Z" fill="url(#handsPhoto)"/>
  </svg>

  <div class="brand"><span class="brand__mark"></span>KOVALIN</div>
  <p class="agent-title">Devan Mehra, Sales Manager</p>
  <ul class="contact-list">
    <li>
      <svg viewBox="0 0 20 20"><circle cx="10" cy="10" r="8.5" fill="none" stroke="var(--white)" stroke-width="1.6"/><path d="M7 5.5l1.6 1.8-.9 1.3c.6 1.3 1.6 2.3 2.9 2.9l1.3-.9 1.8 1.6-1 1.6c-3.5-.3-6.5-3.3-6.8-6.8z" fill="var(--white)"/></svg>
      03 9412 7306
    </li>
    <li>
      <svg viewBox="0 0 20 20"><circle cx="10" cy="10" r="9" fill="var(--white)"/><rect x="5" y="6.5" width="10" height="7" fill="var(--navy)"/><path d="M5 6.5l5 4 5-4" fill="none" stroke="var(--white)" stroke-width="1"/></svg>
      devan.mehra@kovalinrealestate.com.au
    </li>
    <li>
      <svg viewBox="0 0 20 20"><circle cx="10" cy="10" r="8.5" fill="none" stroke="var(--white)" stroke-width="1.6"/><ellipse cx="10" cy="10" rx="3.5" ry="8.5" fill="none" stroke="var(--white)" stroke-width="1.2"/><path d="M1.5 10h17M3 6h14M3 14h14" stroke="var(--white)" stroke-width="1.1"/></svg>
      www.kovalinrealestate.com.au
    </li>
  </ul>
  <p class="office-address">27/486 Brindle Rd Marsden, Victoria, Australia 3047</p>
</section>

</body>
</html>
```